Buch-/eBook-Cover für einen Elternratgeber
Zielgruppe
Buch: Elternratgeber
Titel: Werte lernen
Untertitel: Deinem Kind den richtigen Umgang beibringen
Wir sind der BRAM Verlag und suchen ein passendes Cover für unseren neuen Elternratgeber. Mit diesem Buch möchten wir Eltern unterstützen, ihren Kindern einen guten und verantwortungsvollen Umgang mit Geld zu vermitteln.
Anforderungen an das Cover-Design:
Bitte keinen Comicstil
Das Buch richtet sich an Eltern (nicht kindlich oder verspielt gestalten)
Keine direkte Darstellung von Geld (z. B. keine Münzen, Geldscheine, Sparschweine usw.)
Ob mit oder ohne Personen auf dem Cover: sind wir offen
Farbwahl und Bildsprache: gerne seriös, ansprechend und modern
Wir sind gespannt auf kreative und professionelle Vorschläge!
E-Book E-Book"
Das Design darf nicht zu überladen sein.

```html
<!DOCTYPE html>
<html lang="de">
<head>
<meta charset="utf-8">
<title>Werte lernen – Elternratgeber</title>
<link rel="stylesheet" href="https://fonts.googleapis.com/css2?family=Jost:wght@400;500;600&display=swap">
<style>
  :root {
    --teal-dark: #0a4454;
    --plum: #8a1063;
    --white: #ffffff;
    --sand: #d9c6a4;
    --sea: #4f8596;
    --mist: #dfe5e6;
    --sky: #c6d8e0;
  }
  * { margin: 0; padding: 0; box-sizing: border-box; }
  html, body { width: 750px; height: 1200px; overflow: hidden; background: var(--white); }
  .cover {
    position: relative;
    width: 750px;
    height: 1200px;
    background: var(--white);
    font-family: "Jost", "Futura", sans-serif;
    overflow: hidden;
  }
  .visual { position: absolute; left: 0; width: 750px; }
  .visual--top {
    top: 0; height: 497px;
    background:
      radial-gradient(ellipse at 85% 80%, #fbf5e8 0%, rgba(251,245,232,0) 45%),
      linear-gradient(170deg, #8a7254 0%, #cdb690 22%, #e8dcc6 38%, #7fa2aa 58%, var(--sea) 78%, #9db7bd 100%);
  }
  .visual--middle {
    top: 516px; height: 459px;
    background:
      radial-gradient(ellipse at 20% 20%, #f5efec 0%, rgba(245,239,236,0) 55%),
      linear-gradient(180deg, #eceeed 0%, var(--mist) 45%, var(--sky) 100%);
  }
  .visual--bottom {
    top: 990px; height: 210px;
    background:
      radial-gradient(ellipse at 85% 30%, #fbf5e8 0%, rgba(251,245,232,0) 50%),
      linear-gradient(160deg, #c9b592 0%, #7fa2aa 30%, var(--sea) 60%, #a9c2c6 100%);
  }
  .series-label {
    position: absolute;
    top: 0; left: 0;
    width: 319px; height: 78px;
    background: var(--teal-dark);
    color: var(--white);
    font-weight: 500;
    font-size: 22px;
    letter-spacing: 2.4px;
    line-height: 78px;
    padding-left: 54px;
  }
  .title {
    position: absolute;
    left: 34px; top: 536px;
    color: var(--teal-dark);
    font-weight: 500;
    font-size: 86px;
    line-height: 84px;
    letter-spacing: 3px;
    text-transform: uppercase;
  }
  .subtitle {
    position: absolute;
    left: 44px; top: 842px;
    color: var(--plum);
    font-weight: 500;
    font-size: 42px;
    line-height: 52px;
    letter-spacing: 0.6px;
  }
</style>
</head>
<body>
  <main class="cover">
    <div class="visual visual--top" role="img" aria-label="Unscharfe Szene mit schwebenden hellen Ziffern, Prozentzeichen und Papierblättern in Sand- und Petroltönen"></div>
    <div class="visual visual--middle" role="img" aria-label="Stark aufgehellte, verschwommene Fortsetzung der schwebenden Ziffern und Blätter"></div>
    <div class="visual visual--bottom" role="img" aria-label="Gespiegelter Ausschnitt mit schwebenden Ziffern und Papierblättern"></div>

    <div class="series-label">ELTERNRATGEBER</div>

    <h1 class="title">Werte<br>lernen</h1>
    <p class="subtitle">Deinem Kind den richtigen<br>Umgang beibringen</p>
  </main>
</body>
</html>
```